Marrowby Water Taxi and Transport Business Card

I need business cards for my new water taxi and freight transport business I have started here in Kodiak Alaska. Kodiak is a remote island in the middle of the gulf of Alaska. There are seven native villages around the island and Kodiak is the #2 fishing port in the United States. We also have the largest Coast Guard Base in the U.S. My company will be providing water taxi and freight transport logistics to the villages and many hunting and fishing lodges as well as remote properties around the island.

I would like a business card that isn't status quo, something that stands out, either in feel or appearance. I do like clean minimal designs but it needs to have the necessary contact info on it.

Target Market(s)

remote lodge / property owners, residents of the many villages around Kodiak and any one wanting to enjoy the great outdoors of Kodiak Alaska

Industry/Entity Type

Business

Contact Information for Business Card

I like clean simple designs that aren't cluttered but still provide the necessary information

Colors
0255a3
3277b5
33a4d5
9bcb3c
add136
fbed22
ffc214
f78f20
f37122

Requirements
Must have
• logo and contact info
• Captain Mason Elwick
• www.marrowbyferryline.com
• mason@marrowbyferryline.com

```html
<!DOCTYPE html>
<html lang="en">
<head>
<meta charset="utf-8">
<title>Marrowby Water Taxi and Transport Business Card</title>
<link rel="stylesheet" href="https://fonts.googleapis.com/css2?family=Open+Sans:wght@400;600;700&display=swap">
<style>
  :root {
    --backdrop: #3b3532;
    --card: #0b0b0c;
    --card-edge: #1a1a1c;
    --sky-blue: #33a4d5;
    --deep-blue: #0255a3;
    --sun-orange: #f7931e;
    --text-light: #f2f2f2;
  }
  * { margin: 0; padding: 0; box-sizing: border-box; }
  html, body {
    width: 1200px; height: 844px; overflow: hidden;
    background: var(--backdrop);
    font-family: "Open Sans", Arial, sans-serif;
  }
  .card-set {
    position: absolute; inset: 0;
    display: flex; align-items: center; justify-content: center; gap: 60px;
  }
  .card {
    width: 525px; height: 300px;
    background: var(--card);
    border: 1px solid var(--card-edge);
    border-radius: 4px;
    box-shadow: 0 14px 30px rgba(0,0,0,.45);
    display: flex; flex-direction: column; align-items: center;
  }
  .brand-mark {
    display: flex; align-items: center; gap: 16px;
    font-weight: 700;
  }
  .brand-mark__dot { border-radius: 50%; background: var(--sun-orange); flex: none; }

  .card--front { justify-content: flex-start; padding-top: 40px; }
  .card--front .brand-mark { color: var(--sky-blue); font-size: 26px; line-height: 1.15; }
  .card--front .brand-mark__dot { width: 78px; height: 78px; }
  .card--front .brand-mark__name { max-width: 250px; }

  .holder-name {
    margin-top: 34px;
    color: var(--sky-blue); font-weight: 700; font-size: 21px; line-height: 1.3;
  }
  .contact-list { list-style: none; margin-top: 12px; }
  .contact-list li {
    display: flex; align-items: center; gap: 9px;
    color: var(--text-light); font-size: 15px; line-height: 24px;
  }
  .contact-list svg { width: 13px; height: 13px; flex: none; }

  .card--back { justify-content: center; }
  .card--back .brand-mark { color: var(--deep-blue); font-size: 34px; line-height: 1.12; gap: 20px; }
  .card--back .brand-mark__dot { width: 104px; height: 104px; }
  .card--back .brand-mark__name { max-width: 300px; }
</style>
</head>
<body>
<main class="card-set">
  <section class="card card--front" aria-label="Business card front">
    <div class="brand-mark">
      <span class="brand-mark__dot"></span>
      <span class="brand-mark__name">Marrowby Water Taxi and Transport</span>
    </div>
    <h1 class="holder-name">Captain Mason Elwick</h1>
    <ul class="contact-list">
      <li>
        <svg viewBox="0 0 13 13" aria-hidden="true">
          <rect x="0.5" y="2" width="12" height="9" rx="1" fill="var(--sky-blue)"/>
          <path d="M1 3 L6.5 7.5 L12 3" fill="none" stroke="#0b0b0c" stroke-width="1.2"/>
        </svg>
        mason@marrowbyferryline.com
      </li>
      <li>
        <svg viewBox="0 0 13 13" aria-hidden="true">
          <path d="M5 8 L8 5" stroke="var(--sky-blue)" stroke-width="1.6" stroke-linecap="round"/>
          <path d="M6 3.5 L7.5 2 A2.5 2.5 0 0 1 11 5.5 L9.5 7" fill="none" stroke="var(--sky-blue)" stroke-width="1.6" stroke-linecap="round"/>
          <path d="M7 9.5 L5.5 11 A2.5 2.5 0 0 1 2 7.5 L3.5 6" fill="none" stroke="var(--sky-blue)" stroke-width="1.6" stroke-linecap="round"/>
        </svg>
        www.marrowbyferryline.com
      </li>
    </ul>
  </section>

  <section class="card card--back" aria-label="Business card back">
    <div class="brand-mark">
      <span class="brand-mark__dot"></span>
      <span class="brand-mark__name">Marrowby Water Taxi and Transport</span>
    </div>
  </section>
</main>
</body>
</html>
```